Business card for my new company (Accounting firm)

I need a business card for my new business Brightwell Advisory and Ledger SA. Our services are accounting, tax, audit and financial management. Our customers are small companies, start-ups and new companies. The final design has to show financial security, trust and growth. Please find our logo attached to the business card. Text for the business card: Brightwell Advisory and Ledger SA Tomas Varenholt Director and Founder Certified Accountant Tel. 022 418 57 34 tv@clairevalconseil.ch www.clairevalconseil.ch Rue des Vergières 27 1201 Geneva
Target Market(s)
Our customers are small companies, start-ups and new companies.
Industry/Entity Type
Finance And Accounting
Contact Information for Business Card
Claireval Conseil et Comptes SA
Tomas Varenholt
Directeur et Fondateur
Expert-comptable diplômé
Tél. 022 418 57 34
tv@clairevalconseil.ch
www.clairevalconseil.ch
Rue des Vergières 27
1201 Genève

```html
<!DOCTYPE html>
<html lang="fr">
<head>
<meta charset="utf-8">
<title>Claireval Conseil et Comptes SA – Carte de visite</title>
<link rel="stylesheet" href="https://fonts.googleapis.com/css2?family=Roboto:wght@400;500;700&display=swap">
<style>
  :root {
    --bg: #262626;
    --paper: #ffffff;
    --ink: #3a3a3a;
    --ink-soft: #555555;
    --blue-light: #33aee2;
    --blue-mid: #2089c9;
    --blue-deep: #1a6592;
    --edge: #1f6fa3;
  }
  * { box-sizing: border-box; margin: 0; padding: 0; }
  html, body { width: 1200px; height: 960px; overflow: hidden; }
  body {
    background: var(--bg);
    font-family: "Roboto", Arial, sans-serif;
    display: flex;
    flex-direction: column;
    align-items: center;
    justify-content: center;
    gap: 36px;
  }
  .card {
    width: 740px;
    height: 428px;
    background: var(--paper);
    border-bottom: 6px solid var(--edge);
    position: relative;
    overflow: hidden;
  }

  /* Back side */
  .card--back {
    display: flex;
    flex-direction: column;
    align-items: center;
    justify-content: center;
    gap: 22px;
  }
  .brand-name {
    font-weight: 500;
    color: var(--ink);
    letter-spacing: 0.04em;
  }
  .card--back .brand-name { font-size: 30px; }
  .back-web {
    font-size: 17px;
    letter-spacing: 0.22em;
    color: var(--ink-soft);
  }

  /* Front side */
  .front-mark {
    position: absolute;
    left: 70px;
    top: 64px;
    width: 300px;
    height: 300px;
    border-radius: 50%;
    background: linear-gradient(135deg, var(--blue-light), var(--blue-mid) 55%, var(--blue-deep));
  }
  .front-info {
    position: absolute;
    right: 48px;
    top: 44px;
    text-align: right;
    color: var(--ink);
  }
  .card--front .brand-name {
    font-size: 23px;
    margin-bottom: 26px;
  }
  .person-name {
    font-size: 25px;
    font-weight: 700;
    color: var(--blue-light);
    margin-bottom: 4px;
  }
  .person-role {
    font-size: 17px;
    line-height: 1.3;
    margin-bottom: 16px;
  }
  .address {
    font-size: 17px;
    line-height: 1.3;
    color: var(--ink-soft);
    margin-bottom: 16px;
  }
  .contact-list { list-style: none; }
  .contact-list li {
    font-size: 17px;
    line-height: 1.45;
    color: var(--ink-soft);
    display: flex;
    justify-content: flex-end;
    align-items: center;
    gap: 10px;
  }
  .contact-icon { width: 15px; height: 15px; fill: var(--blue-light); flex: none; }
</style>
</head>
<body>

  <section class="card card--back" aria-label="Verso de la carte">
    <div class="brand-name">Claireval Conseil et Comptes</div>
    <div class="back-web">www.clairevalconseil.ch</div>
  </section>

  <section class="card card--front" aria-label="Recto de la carte">
    <div class="front-mark" role="img" aria-label="Grand motif décoratif bleu de la marque"></div>

    <div class="front-info">
      <div class="brand-name">Claireval Conseil et Comptes</div>
      <div class="person-name">Tomas Varenholt</div>
      <div class="person-role">Directeur et Fondateur<br>Expert-comptable diplômé</div>
      <div class="address">Rue des Vergières 27<br>1201 Genève</div>
      <ul class="contact-list">
        <li>022 418 57 34
          <svg class="contact-icon" viewBox="0 0 24 24" aria-hidden="true"><path d="M6.6 10.8a15.1 15.1 0 0 0 6.6 6.6l2.2-2.2a1 1 0 0 1 1-.25 11.4 11.4 0 0 0 3.6.57 1 1 0 0 1 1 1V20a1 1 0 0 1-1 1A17 17 0 0 1 3 4a1 1 0 0 1 1-1h3.5a1 1 0 0 1 1 1c0 1.25.2 2.45.57 3.57a1 1 0 0 1-.25 1z"/></svg>
        </li>
        <li>tv@clairevalconseil.ch
          <svg class="contact-icon" viewBox="0 0 24 24" aria-hidden="true"><path d="M2 5h20v14H2z M3.5 6.5 12 12.5l8.5-6" fill="var(--blue-light)" stroke="#fff" stroke-width="1.5"/></svg>
        </li>
        <li>www.clairevalconseil.ch
          <svg class="contact-icon" viewBox="0 0 24 24" aria-hidden="true"><circle cx="12" cy="12" r="10"/><path d="M2 12h20M12 2c3 3 3 17 0 20M12 2c-3 3-3 17 0 20" fill="none" stroke="#fff" stroke-width="1.4"/></svg>
        </li>
      </ul>
    </div>
  </section>

</body>
</html>
```